Podcast Cover Art for rebranded podcast - I have inspiration for the designs

I've had a podcast ("Paperboat Radio Hour") since 2018, but I'm in the process of rebranding it. I've attached the old cover art below, which I loved, but I don't need it to look like that at all. The rebranded podcast is called 'Open Window with Marnie Cole.' I've included the show description at the bottom. I've been working on various design options in Canva, but not obsessed with anything yet, but I'm attaching the ones I do like that I think just need some refining. My very favorite is the one labeled 'favorite_Open Window' so I wouldn't mind keeping that general idea but perfected by a designer. Ultimately, I want something cool, fairly clean, modern, eye catching. I'm into neutrals with maybe a pop of color, so think black, white, grey..maybe silver, and I love a pop of red..and I'm not opposed to other options for the pop color. The show is going to be inspiring, entertaining, and funny. Oh and one other idea I had but I'm not sure if it makes sense with the title and/or what the show is about..but a vinyl record with Open Window with Marnie Cole on it somehow, on a record player..not sure.

Ever wonder what it means to truly live authentically? Curious about how to embrace the unpredictability of life? Ready for some heartfelt and lighthearted conversations that inspire and entertain?
Join Marnie Cole as she dives into the raw, real, and unscripted moments of life. In each episode, Marnie brings candid conversations and genuine insights into the ups and downs we all experience. From personal growth and self-discovery to inspiring stories and valuable life lessons, "Open Window" is a space where authenticity reigns and spontaneity is celebrated.
Whether she's sharing her own journey or chatting with inspiring guests, Marnie invites you to explore the beauty of living life without a script. Expect honest reflections, thought-provoking discussions, and a refreshing perspective on navigating life's unpredictable path—all with a dash of fun and humor to keep things lively and entertaining. Step into the unscripted moments of life and tune in for a blend of depth and lightheartedness that will leave you inspired, smiling, and most importantly laughing.

Target Market(s)

25-50 year old women and men (primarily women)

Font styles to use
Sans Serif

Requirements
Should not have
• nothing too feminine or girly, nothing cheesy :)

```html
<!DOCTYPE html>
<html lang="en">
<head>
<meta charset="utf-8">
<title>Open Window with Marnie Cole — Podcast Cover</title>
<link href="https://fonts.googleapis.com/css2?family=Anton&family=Kaushan+Script&family=Allura&family=Oswald:wght@300;700&family=Poppins:wght@400&display=swap" rel="stylesheet">
<style>
  :root {
    --cover-white: #f4f4f4;
    --mist-grey: #e2e2e2;
    --sea-grey: #cfcfcf;
    --signal-red: #d90a2c;
    --ink-black: #0b0b0b;
    --strip-black: #050505;
  }
  html, body {
    margin: 0;
    padding: 0;
    width: 1200px;
    height: 1200px;
    overflow: hidden;
    background: var(--cover-white);
  }
  .cover {
    position: relative;
    width: 1200px;
    height: 1200px;
    overflow: hidden;
    background: var(--cover-white);
  }
  .beach-backdrop {
    position: absolute;
    inset: 0;
    background:
      linear-gradient(180deg, #ececec 0%, #e6e6e6 26%, #d8d8d8 27%, #dcdcdc 40%, #efefef 55%, #f6f6f6 100%);
  }
  .title-art {
    position: absolute;
    left: 0;
    top: 0;
    width: 771px;
    height: 1200px;
  }
  .title-word {
    font-family: "Anton", "Impact", sans-serif;
    fill: var(--signal-red);
  }
  .title-script {
    font-family: "Kaushan Script", cursive;
    fill: var(--ink-black);
    stroke: #ffffff;
    stroke-width: 14px;
    stroke-linejoin: round;
    paint-order: stroke fill;
  }
  .host-with {
    font-family: "Allura", cursive;
    fill: var(--signal-red);
  }
  .host-first {
    font-family: "Oswald", sans-serif;
    font-weight: 700;
    fill: var(--ink-black);
  }
  .host-last {
    font-family: "Oswald", sans-serif;
    font-weight: 300;
    fill: var(--ink-black);
  }
  .show-label {
    font-family: "Poppins", sans-serif;
    font-weight: 400;
    fill: var(--ink-black);
    letter-spacing: 6px;
  }
  .film-strip {
    position: absolute;
    left: 771px;
    top: 0;
    width: 340px;
    height: 1200px;
    background: var(--strip-black);
  }
  .film-frame {
    position: absolute;
    left: 19px;
    width: 301px;
    border-radius: 7px;
  }
  .frame-studio {
    top: 0;
    height: 284px;
    border-radius: 0 0 7px 7px;
    background: linear-gradient(160deg, #8a8a8a 0%, #3a3a3a 55%, #1c1c1c 100%);
  }
  .frame-red-room {
    top: 317px;
    height: 308px;
    background: linear-gradient(150deg, #c20a0a 0%, #7a0505 50%, #2a0202 100%);
  }
  .frame-bedroom {
    top: 653px;
    height: 308px;
    background: linear-gradient(180deg, #cfcfcf 0%, #f2f2f2 45%, #e6e6e6 100%);
  }
  .frame-garden {
    top: 990px;
    height: 210px;
    border-radius: 7px 7px 0 0;
    background: linear-gradient(160deg, #6f7a2c 0%, #3b4219 45%, #a89a7a 100%);
  }
  .edge-margin {
    position: absolute;
    left: 1111px;
    top: 0;
    width: 89px;
    height: 1200px;
    background: linear-gradient(180deg, #efefef 0%, #e4e4e4 35%, #f3f3f3 100%);
  }
</style>
</head>
<body>
  <main class="cover">
    <div class="beach-backdrop" role="img" aria-label="Faded black and white photo of the host walking on a beach toward the sea"></div>

    <svg class="title-art" viewBox="0 0 771 1200" xmlns="http://www.w3.org/2000/svg" aria-label="Open Window with Marnie Cole podcast">
      <text class="title-word" x="95" y="462" font-size="400" textLength="516" lengthAdjust="spacingAndGlyphs">OPEN</text>
      <text class="title-script" x="110" y="640" font-size="210" textLength="600" lengthAdjust="spacingAndGlyphs" transform="rotate(-9 110 640)">Window</text>
      <text class="host-with" x="95" y="805" font-size="110">with</text>
      <text class="host-first" x="93" y="920" font-size="116" textLength="238" lengthAdjust="spacingAndGlyphs">MARNIE</text>
      <text class="host-last" x="347" y="920" font-size="116" textLength="200" lengthAdjust="spacingAndGlyphs">COLE</text>
      <text class="show-label" x="95" y="1068" font-size="26">PODCAST</text>
    </svg>

    <div class="film-strip">
      <div class="film-frame frame-studio" role="img" aria-label="Black and white photo of the host recording with headphones"></div>
      <div class="film-frame frame-red-room" role="img" aria-label="Red-toned photo of the host seated in a lounge"></div>
      <div class="film-frame frame-bedroom" role="img" aria-label="Black and white photo of the host lying on a white bed"></div>
      <div class="film-frame frame-garden" role="img" aria-label="Colour photo of the host sitting outdoors in a sunny garden"></div>
    </div>

    <div class="edge-margin" role="img" aria-label="Continuation of the faded beach photo"></div>
  </main>
</body>
</html>
```